HOT TUB - SPAS service needs an business card

I need an business for my company who his specialise in a maintenance,water treatment and cleaning of Hot Tub - Spas for commercial and residential customers. The company operate mainly in the ski resort of Chamonix, Megève and St Gervais. The final product should communicate pure water, cleanest and professional for luxury property's.
I have upload a logo but any improvement on it is welcome.(color,size, details etc..) or any other idea. Thank you
Company Name: 58 BAINS
My name: Lucien Marchetti
Email: lucimarch@examplemail.net
Tel: +33 (0)6 71 58 29 64
Description to be on the card in french(first langage) and in English:
- Spas service
- Entretien, traitement eau, nettoyage.
- Maintenance, water treatment, cleaning.
Industry/Entity Type
Residential
Colors
Designer to choose colors to be used in the design.
Look and feel
Each slider illustrates characteristics of the customer's brand and the style your logo design should communicate.

```html
<!DOCTYPE html>
<html lang="fr">
<head>
<meta charset="utf-8">
<title>58 BAINS – Business Card</title>
<link rel="stylesheet" href="https://fonts.googleapis.com/css2?family=Open+Sans:wght@400;600;700&display=swap">
<style>
  :root {
    --page-bg: #e8ebee;
    --front-sky: #22a4f7;
    --front-house: #0f5fc9;
    --back-blue: #0f78d8;
    --ink-white: #ffffff;
    --font-main: "Open Sans", Arial, sans-serif;
  }
  * { box-sizing: border-box; margin: 0; padding: 0; }
  html, body {
    width: 1200px; height: 1100px; overflow: hidden;
    background: var(--page-bg);
    font-family: var(--font-main);
    color: var(--ink-white);
  }
  .canvas { position: relative; width: 1200px; height: 1100px; }
  .card {
    position: absolute; width: 830px; height: 473px; overflow: hidden;
    box-shadow: 0 6px 18px rgba(0,0,0,.18);
  }
  .card--front { left: 40px; top: 40px; background: var(--front-sky); }
  .card--back  { left: 330px; top: 590px; background: var(--back-blue); }

  .card__house-band { position: absolute; inset: 0; width: 830px; height: 473px; }

  .brand-mark {
    position: absolute; left: 0; right: 0;
    display: flex; align-items: center; justify-content: center; gap: 18px;
    font-weight: 600; font-size: 58px; letter-spacing: 4px; line-height: 1;
  }
  .brand-mark__dot {
    width: 22px; height: 22px; border-radius: 50%; background: var(--ink-white);
  }
  .card--front .brand-mark { top: 95px; }
  .card--back  .brand-mark { top: 150px; }

  .centered { position: absolute; left: 0; right: 0; text-align: center; white-space: nowrap; }

  .company-name { top: 208px; font-size: 37px; font-weight: 700; }
  .owner-name   { top: 320px; font-size: 27px; font-weight: 700; }
  .contact {
    display: flex; align-items: center; justify-content: center; gap: 10px;
    font-size: 25px; font-weight: 400;
  }
  .contact--phone { top: 368px; font-weight: 600; }
  .contact--email { top: 410px; }
  .contact__icon { width: 22px; height: 22px; flex: none; }

  .services-title { top: 330px; font-size: 28px; font-weight: 700; }
  .services-line  { font-size: 26px; font-weight: 400; }
  .services-line--fr { top: 377px; }
  .services-line--en { top: 416px; }
</style>
</head>
<body>
<main class="canvas">

  <section class="card card--front" aria-label="Recto de la carte">
    <svg class="card__house-band" viewBox="0 0 830 473" aria-hidden="true">
      <polygon points="0,335 411,263 830,335 787,335 787,473 41,473 41,335" fill="var(--front-house)"/>
    </svg>

    <div class="brand-mark"><span class="brand-mark__dot"></span>58 BAINS</div>

    <h1 class="centered company-name">58 BAINS</h1>
    <p class="centered owner-name">Lucien Marchetti</p>
    <p class="centered contact contact--phone">
      <svg class="contact__icon" viewBox="0 0 24 24" aria-hidden="true">
        <circle cx="12" cy="12" r="10.5" fill="none" stroke="#fff" stroke-width="1.6"/>
        <path d="M8.5 6.5c-1.5 1-1.6 3.8.6 7 2.2 3.2 4.8 4.4 6.3 3.6l.9-.6-2-2.6-1.4.6c-.8-.4-2-2-2.4-3l1-1.1-1.6-2.9z" fill="#fff"/>
      </svg>
      +33 (0)6 71 58 29 64
    </p>
    <p class="centered contact contact--email">
      <svg class="contact__icon" viewBox="0 0 24 24" aria-hidden="true">
        <path d="M2 10 12 3l10 7v10H2z" fill="#fff"/>
        <path d="M2 10l10 6 10-6" fill="none" stroke="var(--front-house)" stroke-width="1.4"/>
        <rect x="7" y="7" width="10" height="5" fill="var(--front-house)"/>
      </svg>
      lucimarch@examplemail.net
    </p>
  </section>

  <section class="card card--back" aria-label="Verso de la carte">
    <div class="brand-mark"><span class="brand-mark__dot"></span>58 BAINS</div>

    <h2 class="centered services-title">SPAS SERVICES</h2>
    <p class="centered services-line services-line--fr">•Entretien &nbsp;•traitement eau &nbsp;•nettoyage</p>
    <p class="centered services-line services-line--en">•Maintenance &nbsp;•water treatment &nbsp;•cleaning.</p>
  </section>

</main>
</body>
</html>
```